BrindleStaffing Business Card Design

We are a staffing company finding positions for dedicated nurses and physicians.

Target Market(s)

Business Professionals

Industry/Entity Type

Staffing

Contact Information for Business Card

Gordon Pratley
Chairman
417 39th Avenue South
SAINT PETERSBURG FL 33712
813-555-4172 Mobile
813-555-8036 Fax
gpratley@brindlestaffing.com
www.brindlestaffing.com

Font styles to use
Sans Serif

Colors
fbee3e
f04a50
f37122

Requirements
Must have
• Logo Attached, see colors below. We'd like to see Yellow, Orange and Red.

```html
<!DOCTYPE html>
<html lang="en">
<head>
<meta charset="utf-8">
<title>BrindleStaffing Business Card</title>
<link rel="stylesheet" href="https://fonts.googleapis.com/css2?family=Open+Sans:wght@400;600&family=Poppins:wght@700&display=swap">
<style>
  :root {
    --bg-light: #97979a;
    --bg-dark: #48484a;
    --card: #ffffff;
    --brand-red: #f04a50;
    --brand-orange: #f37122;
    --brand-yellow: #fbee3e;
    --ink: #222326;
    --rule: #9a9a9a;
    --band: #fdf3dc;
  }
  html, body {
    margin: 0;
    width: 1200px;
    height: 1134px;
    overflow: hidden;
  }
  body {
    position: relative;
    background: radial-gradient(circle at 50% 50%, var(--bg-light) 0%, var(--bg-dark) 85%);
    font-family: "Open Sans", sans-serif;
  }
  .card {
    position: absolute;
    width: 715px;
    height: 409px;
    border-radius: 36px;
    background: var(--card);
    overflow: hidden;
    box-shadow: 0 2px 6px rgba(0,0,0,0.25);
  }
  .card svg { display: block; width: 100%; height: 100%; }
  .card-front { left: 388px; top: 98px; }
  .card-back { left: 137px; top: 599px; }
  .wordmark { font-family: "Poppins", sans-serif; font-weight: 700; fill: var(--brand-red); }
  .person-name { font-weight: 600; fill: var(--brand-red); font-size: 26px; }
  .person-title { fill: var(--brand-orange); font-size: 22px; }
  .address, .contact { fill: var(--ink); font-size: 20px; }
  .site-url { font-size: 24px; letter-spacing: 3px; fill: var(--ink); }
  .site-url .url-name-a { fill: var(--brand-orange); font-weight: 600; }
  .site-url .url-name-b { fill: var(--brand-red); font-weight: 600; }
  .icon { fill: none; stroke: var(--brand-orange); stroke-width: 1.6; }
  .icon-solid { fill: var(--brand-orange); stroke: none; }
</style>
</head>
<body>

<div class="card card-front">
  <svg viewBox="0 0 785 449" aria-label="Business card front">
    <text class="wordmark" x="391" y="135" font-size="60" text-anchor="middle">BrindleStaffing</text>
    <circle cx="640" cy="88" r="8" fill="var(--brand-orange)"/>

    <text class="person-name" x="340" y="220" text-anchor="end">Gordon Pratley</text>
    <text class="person-title" x="340" y="250" text-anchor="end">Title</text>
    <text class="address" x="340" y="279" text-anchor="end">417 39th avenue south</text>
    <text class="address" x="340" y="306" text-anchor="end">Saint petersburg fl 33712</text>

    <line x1="365" y1="205" x2="365" y2="308" stroke="var(--rule)" stroke-width="1"/>

    <g class="icon">
      <circle cx="394" cy="213" r="8"/>
      <path class="icon-solid" d="M391 208 q-2 5 1 9 l2 -1 -1 -3 q1 -3 3 -4 l-1 -2 z"/>
      <rect class="icon-solid" x="386" y="252" width="16" height="10"/>
      <path d="M386 252 l8 -5 l8 5"/>
      <path d="M386 253 l8 5 l8 -5" stroke="#fff"/>
      <circle cx="394" cy="297" r="8"/>
      <path d="M386 297 h16 M394 289 q-5 8 0 16 M394 289 q5 8 0 16"/>
    </g>
    <text class="contact" x="414" y="220">813-555-4172</text>
    <text class="contact" x="414" y="262">gpratley@brindlestaffing.com</text>
    <text class="contact" x="414" y="304">www.brindlestaffing.com</text>

    <path d="M0 308 C150 370 400 415 575 418 C400 422 150 395 0 352 Z" fill="var(--brand-orange)"/>
    <path d="M0 360 C200 405 500 432 695 409 L602 449 L0 449 Z" fill="var(--brand-red)"/>
    <path d="M610 449 L785 382 L785 449 Z" fill="var(--brand-yellow)"/>
  </svg>
</div>

<div class="card card-back">
  <svg viewBox="0 0 785 449" aria-label="Business card back">
    <rect class="band-vertical" x="315" y="0" width="180" height="449" fill="var(--band)"/>
    <rect class="band-horizontal" x="180" y="134" width="449" height="179" fill="var(--band)"/>
    <text class="wordmark" x="391" y="231" font-size="72" text-anchor="middle">BrindleStaffing</text>
    <text class="site-url" x="391" y="293" text-anchor="middle">www.<tspan class="url-name-a">brindle</tspan><tspan class="url-name-b">staffing</tspan>.com</text>
  </svg>
</div>

</body>
</html>
```